Penfield Draft Works (PDWorks.net)

We need a Wordpress-based site designed for a client who provides writing and editing services for the IT industry. We have a wireframe complete for the homepage, but need all internal pages designed (based on homepage wireframe) and the entire site coded for WP.

Internal pages include: "Our Work" (with samples & testimonials); "Capabilities" (with sections to address "strategy", "coaching", "writing" and "editing"); "About Us"; and a Contact page.

Will provide all copywriting, writing samples, testimonials, and client logos.

We completely realize/acknowledge the subject matter is visually BORING! Anything at all that can be done to make it look visually appealing would be *great*! Stock photography is fine.

Please feel free to ask any questions whatsoever. Thanks for your time!

```html
<!DOCTYPE html>
<html lang="en">
<head>
<meta charset="utf-8">
<title>Penfield Draft Works</title>
<link rel="stylesheet" href="https://fonts.googleapis.com/css2?family=Montserrat:wght@500;600;700;800&family=Nunito+Sans:wght@400;600&display=swap">
<style>
:root{
  --accent:#e8441e;
  --ink:#1c1c1c;
  --body:#3a3a3a;
  --soft-bg:#f5f1f1;
  --works-bg:#dcd9d9;
  --band-left:#333232;
  --band-right:#2b2a2a;
  --footer:#141414;
  --white:#ffffff;
  --line:#d9d4d4;
}
*{box-sizing:border-box;margin:0;padding:0}
html,body{width:1200px;height:2818px;overflow:hidden}
body{font-family:"Nunito Sans",sans-serif;color:var(--body);background:var(--white);position:relative}
.heading{font-family:"Montserrat",sans-serif}
section,header,footer{position:absolute;left:0;width:1200px}

/* hero */
.hero{top:0;height:680px;overflow:hidden}
.hero-photo{position:absolute;inset:0;background:radial-gradient(ellipse at 55% 55%,#8f8a84 0%,#6f6a64 45%,#3f3c39 100%)}
.hero-shade{position:absolute;inset:0;background:rgba(20,18,16,.35)}
.brand{position:absolute;left:47px;top:30px;font-family:"Montserrat",sans-serif;font-weight:700;font-size:22px;color:var(--white)}
.nav{position:absolute;top:34px;left:557px;display:flex;gap:0;font-family:"Montserrat",sans-serif;font-weight:600;font-size:15px;color:var(--white)}
.nav a{color:inherit;text-decoration:none;position:absolute;white-space:nowrap}
.nav a.active::after{content:"";position:absolute;left:0;right:0;bottom:-6px;height:2px;background:var(--white)}
.nav-cta{position:absolute;left:1028px;top:27px;width:118px;height:36px;border:2px solid var(--white);border-radius:5px;color:var(--white);font-family:"Montserrat",sans-serif;font-weight:600;font-size:15px;display:flex;align-items:center;justify-content:center}
.hero-title{position:absolute;top:226px;left:0;width:1200px;text-align:center;color:var(--white);font-family:"Montserrat",sans-serif;font-weight:800;font-size:34px;line-height:49px;text-transform:uppercase;text-shadow:0 2px 6px rgba(0,0,0,.4)}
.dots{position:absolute;top:632px;left:0;width:1200px;display:flex;justify-content:center;align-items:center;gap:12px}
.dots span{width:6px;height:6px;border-radius:50%;background:var(--white)}
.dots span.on{width:12px;height:12px;background:none;border:2px solid var(--white)}

/* services */
.services{top:680px;height:600px;background:var(--soft-bg)}
.section-title{position:absolute;left:0;width:1200px;text-align:center;font-family:"Montserrat",sans-serif;font-weight:600;color:var(--ink)}
.services .section-title{top:42px;font-size:24px;line-height:37px}
.service-card{position:absolute;top:159px;width:226px;height:301px;background:var(--white);border-radius:4px;box-shadow:0 1px 6px rgba(0,0,0,.12);text-align:center;padding-top:36px}
.service-card svg{width:56px;height:56px}
.service-name{font-family:"Montserrat",sans-serif;font-weight:500;font-size:17px;color:var(--ink);margin-top:20px}
.service-text{font-size:12.5px;line-height:17.5px;color:#333;margin:22px 20px 0}
.btn{position:absolute;background:var(--accent);color:var(--white);font-family:"Montserrat",sans-serif;font-weight:600;border-radius:4px;display:flex;align-items:center;justify-content:center}
.services .btn{left:501px;top:505px;width:198px;height:47px;font-size:16px}

/* clients */
.clients{top:1280px;height:292px;background:var(--white)}
.clients .section-title{top:62px;font-size:23px}
.client-box{position:absolute;top:135px;width:178px;height:84px;border:1px solid var(--line);border-radius:4px;display:flex;align-items:center;justify-content:center;gap:8px;font-family:"Montserrat",sans-serif;font-weight:700;font-size:18px;color:#2a2a2a}
.client-box i{width:12px;height:12px;background:#2a2a2a;display:inline-block}

/* works */
.works{top:1572px;height:643px;background:linear-gradient(180deg,#d6d3d3 0%,var(--works-bg) 60%,#d3d0d0 100%)}
.works .section-title{top:40px;font-size:23px}
.work-card{position:absolute;top:107px;width:304px;height:406px;background:var(--white);border-radius:4px;overflow:hidden}
.work-photo{height:175px}
.work-body{padding:24px 26px 0}
.work-title{font-family:"Montserrat",sans-serif;font-weight:600;font-size:14.5px;line-height:21px;color:var(--ink)}
.work-text{font-size:12.5px;line-height:19px;color:#333;margin-top:14px}
.read-more{display:inline-block;margin-top:20px;background:var(--accent);color:var(--white);font-family:"Montserrat",sans-serif;font-weight:600;font-size:10px;padding:6px 9px;border-radius:3px}
.works .btn{left:528px;top:552px;width:144px;height:43px;font-size:15px}

/* contact band */
.contact-band{top:2215px;height:255px;display:flex}
.band-half{width:600px;height:255px;position:relative;text-align:center;color:var(--white)}
.band-left{background:var(--band-left);width:592px}
.band-right{background:var(--band-right);width:608px}
.band-title{position:absolute;top:58px;left:0;width:100%;font-family:"Montserrat",sans-serif;font-weight:600;font-size:21px;line-height:34px}
.band-left .btn{left:271px;top:153px;width:137px;height:42px;font-size:15px}
.email-field{position:absolute;left:99px;top:153px;width:313px;height:44px;background:#1f1e1e;border-radius:3px;display:flex;align-items:center;gap:10px;padding-left:20px;font-size:12px;color:#ddd}

/* footer */
.site-footer{top:2470px;height:348px;background:var(--footer);color:#e6e6e6}
.footer-brand{position:absolute;left:133px;top:118px;font-family:"Montserrat",sans-serif;font-weight:700;font-size:22px;color:var(--white)}
.footer-col{position:absolute;top:53px}
.footer-head{font-family:"Montserrat",sans-serif;font-weight:700;font-size:12px;letter-spacing:.5px;color:var(--white)}
.footer-menu{list-style:none;margin-top:22px;font-size:12px;line-height:20px;text-transform:uppercase}
.footer-item{display:flex;gap:10px;align-items:flex-start;margin-top:18px;font-size:12px;line-height:16px}
.footer-item:first-of-type{margin-top:22px}
.footer-item .dot{width:24px;height:24px;border-radius:50%;background:var(--white);flex:none;display:flex;align-items:center;justify-content:center}
.footer-rule{position:absolute;left:133px;top:268px;width:934px;height:1px;background:#2e2e2e}
.copyright{position:absolute;top:306px;left:0;width:1200px;text-align:center;font-size:10px;color:#ddd}
</style>
</head>
<body>

<header class="hero">
  <div class="hero-photo" role="img" aria-label="Photo of a wooden desk from above with hands writing in a notebook beside a laptop and patterned folders"></div>
  <div class="hero-shade"></div>
  <div class="brand">Penfield Draft Works</div>
  <nav class="nav">
    <a class="active" style="left:0">Home</a>
    <a style="left:78px">Our Work</a>
    <a style="left:184px">Capabilities</a>
    <a style="left:313px">About us</a>
    <a style="left:410px">Blog</a>
  </nav>
  <div class="nav-cta">Get in Touch</div>
  <h1 class="hero-title">Communicate your expertise<br>and your customer successes</h1>
  <div class="dots"><span></span><span></span><span class="on"></span><span></span><span></span></div>
</header>

<section class="services">
  <h2 class="section-title">Text Copy that explains in concise, snappy terms<br>the value you provide to customers.</h2>

  <article class="service-card" style="left:120px">
    <svg viewBox="0 0 56 56" fill="none" stroke="var(--accent)" stroke-width="2.2"><rect x="4" y="4" width="48" height="34"/><path d="M2 4h52M12 30l10-10 8 6 12-12M28 38v6M16 52l12-8 12 8"/></svg>
    <div class="service-name">Strategy</div>
    <p class="service-text">Lorem ipsum dolor sit amet consectetur adipiscing elit sed do eiusmod tempor inc ididunt ut labor. Ut enim ad minim veniam quis nostrud exerc itation ullamc.</p>
  </article>
  <article class="service-card" style="left:366px">
    <svg viewBox="0 0 56 56" fill="none" stroke="var(--accent)" stroke-width="2.2"><rect x="22" y="3" width="28" height="20" rx="2"/><path d="M27 10h18M27 16h12"/><rect x="8" y="20" width="30" height="24" rx="2"/><circle cx="18" cy="30" r="4"/><path d="M12 40c2-4 10-4 12 0M28 28h6M28 34h6M4 52h48M10 44v8M36 44v8"/></svg>
    <div class="service-name">Coaching</div>
    <p class="service-text">Lorem ipsum dolor sit amet consectetur adipiscing elit sed do eiusmod tempor inc ididunt ut labor. Ut enim ad minim veniam quis nostrud exerc itation ullamc.</p>
  </article>
  <article class="service-card" style="left:610px">
    <svg viewBox="0 0 56 56" fill="none" stroke="var(--accent)" stroke-width="2.2"><path d="M36 30v22H8V4h20l8 8v6"/><path d="M28 4v8h8M14 20h16M14 28h12M14 36h10M14 44h8"/><path d="M48 20l4 4-16 16-6 2 2-6z"/></svg>
    <div class="service-name">Writing</div>
    <p class="service-text">Lorem ipsum dolor sit amet consectetur adipiscing elit sed do eiusmod tempor inc ididunt ut labor. Ut enim ad minim veniam quis nostrud exerc itation ullamc.</p>
  </article>
  <article class="service-card" style="left:853px">
    <svg viewBox="0 0 56 56" fill="none" stroke="var(--accent)" stroke-width="3"><path d="M44 32v18H6V12h18"/><path d="M44 4l8 8-24 24-10 2 2-10z"/></svg>
    <div class="service-name">Editing</div>
    <p class="service-text">Lorem ipsum dolor sit amet consectetur adipiscing elit sed do eiusmod tempor inc ididunt ut labor. Ut enim ad minim veniam quis nostrud exerc itation ullamc.</p>
  </article>

  <div class="btn">View our Capabilities</div>
</section>

<section class="clients">
  <h2 class="section-title">A Selection of Past and Current Clients</h2>
  <div class="client-box" style="left:131px"><i></i>Northgate</div>
  <div class="client-box" style="left:321px">Parcelwise</div>
  <div class="client-box" style="left:511px">Docket Trail</div>
  <div class="client-box" style="left:701px">Huddlebase</div>
  <div class="client-box" style="left:890px">Gatherly</div>
</section>

<section class="works">
  <h2 class="section-title">Our Works</h2>
  <article class="work-card" style="left:131px">
    <div class="work-photo" role="img" aria-label="Photo of hands typing on a laptop on a wooden desk" style="background:linear-gradient(135deg,#6b4a36,#a89a90 55%,#4b3528)"></div>
    <div class="work-body">
      <h3 class="work-title">Lorem Ipsum is simply dummy text of the printing</h3>
      <p class="work-text">Lorem ipsum dolor sit amet, consectetur adipiscing elit, sed do eiusmod tempor incididunt ut labore et dolore magna aliqua. Ut enim ad minim veniam.</p>
      <span class="read-more">Read More</span>
    </div>
  </article>
  <article class="work-card" style="left:448px">
    <div class="work-photo" role="img" aria-label="Photo of a laptop, notebook, coffee cup and phone on a wooden desk seen from above" style="background:linear-gradient(135deg,#5a4334,#8a7766 50%,#3e2f25)"></div>
    <div class="work-body">
      <h3 class="work-title">Lorem Ipsum is simply dummy text of the printing</h3>
      <p class="work-text">Lorem ipsum dolor sit amet, consectetur adipiscing elit, sed do eiusmod tempor incididunt ut labore et dolore magna aliqua. Ut enim ad minim veniam.</p>
      <span class="read-more">Read More</span>
    </div>
  </article>
  <article class="work-card" style="left:765px">
    <div class="work-photo" role="img" aria-label="Illustration of glowing technology icons around a central circle on a dark blue background" style="background:radial-gradient(circle at 50% 45%,#2c6f8f 0%,#0f2c48 45%,#061526 100%)"></div>
    <div class="work-body">
      <h3 class="work-title">Lorem Ipsum is simply dummy text of the printing</h3>
      <p class="work-text">Lorem ipsum dolor sit amet, consectetur adipiscing elit, sed do eiusmod tempor incididunt ut labore et dolore magna aliqua. Ut enim ad minim veniam.</p>
      <span class="read-more">Read More</span>
    </div>
  </article>
  <div class="btn">View our Works</div>
</section>

<section class="contact-band">
  <div class="band-half band-left">
    <h2 class="band-title">Feel free to contact us with<br>any questions, We're happy to help</h2>
    <div class="btn">Get in Touch</div>
  </div>
  <div class="band-half band-right">
    <h2 class="band-title">Editorial Inspiration delivered<br>straight to your inbox</h2>
    <div class="email-field">
      <svg width="11" height="9" viewBox="0 0 11 9"><rect width="11" height="9" rx="1" fill="#ddd"/><path d="M0 1l5.5 4L11 1" stroke="#1f1e1e" fill="none"/></svg>
      Email Address
    </div>
  </div>
</section>

<footer class="site-footer">
  <div class="footer-brand">Penfield Draft Works</div>

  <div class="footer-col" style="left:479px">
    <div class="footer-head">MENU</div>
    <ul class="footer-menu">
      <li>Home</li><li>Our Work</li><li>Capabilities</li><li>About us</li><li>Blog</li><li>Get in Touch</li>
    </ul>
  </div>

  <div class="footer-col" style="left:682px">
    <div class="footer-head">CONTACT US</div>
    <div class="footer-item"><span class="dot"><svg width="10" height="13" viewBox="0 0 10 13"><path d="M5 0a5 5 0 015 5c0 3-5 8-5 8S0 8 0 5a5 5 0 015-5z" fill="#141414"/><circle cx="5" cy="5" r="1.8" fill="#fff"/></svg></span><span>2150 Alder Row<br>Marlow, OR 97402</span></div>
    <div class="footer-item"><span class="dot"><svg width="12" height="12" viewBox="0 0 12 12"><path d="M2 0l3 3-1.5 1.5a7 7 0 004 4L9 7l3 3-2 2C5 12 0 7 0 2z" fill="#141414"/></svg></span><span>Call Us<br>555.014.2290</span></div>
    <div class="footer-item"><span class="dot"><svg width="12" height="9" viewBox="0 0 12 9"><rect width="12" height="9" rx="1" fill="#141414"/><path d="M0 1l6 4 6-4" stroke="#fff" fill="none"/></svg></span><span>E mail Us<br>info@pdworks.net</span></div>
  </div>

  <div class="footer-col" style="left:962px">
    <div class="footer-head">FOLLOW US</div>
    <div class="footer-item"><span class="dot"></span><span>Like us on<br>PAGEBOOK</span></div>
    <div class="footer-item"><span class="dot"></span><span>Follow us on<br>CHIRPLINE</span></div>
    <div class="footer-item"><span class="dot"></span><span>Follow us on<br>WORKLINK</span></div>
  </div>

  <div class="footer-rule"></div>
  <div class="copyright">Copyright © 2021 All Rights Reserved</div>
</footer>

</body>
</html>
```